Profesional personal website needs design and business card

I need a business card with my professional name as a logo "Dorian Vitality" for my business. I am a Wellness Coach, consultant and trainer. So it should be professional, wellness oriented and modern.

Target Market(s)

Private clients, governments, corporations. Luxury and high market.

Industry/Entity Type

Health And Wellness

Contact Information for Business Card

Dorian Vitality should be the logo

Colors

Designer to choose colors to be used in the design.

Requirements
Must have
• Dorian Vitality
• Name: Tomás Lirandel
• Wellness Coach, Consultant & Trainer.
• Website: www.dorianvitality-example.com
• Phone:
• Spain (+34) 612 480 317
• (USA) +1 (555) 610 4829
Nice to have
• The most important is the design of "Dorian Vitality", as this is going to be my personal brand logo. It should be professional, wellness, high end and actual.
Should not have
• no golds, no baroque style..

```html
<!DOCTYPE html>
<html lang="en">
<head>
<meta charset="utf-8">
<title>Dorian Vitality – Business Card</title>
<link rel="stylesheet" href="https://fonts.googleapis.com/css2?family=Arimo:wght@400;700&display=swap">
<style>
  :root {
    --page-bg: #e9ecef;
    --blue-light: #24a6e0;
    --blue-deep: #2563b8;
    --blue-brand: #1f78c8;
    --green-brand: #4aa82a;
    --green-light: #78c043;
    --ink: #555b61;
    --rule: #8a8f94;
    --white: #ffffff;
    --faint-circle: #e6f0f8;
  }
  * { box-sizing: border-box; margin: 0; padding: 0; }
  html, body { width: 1200px; height: 800px; overflow: hidden; }
  body {
    background: var(--page-bg);
    font-family: "Arimo", Arial, sans-serif;
    display: flex;
    align-items: center;
    justify-content: center;
    gap: 60px;
  }
  .card {
    position: relative;
    width: 525px;
    height: 300px;
    border-radius: 16px;
    overflow: hidden;
    box-shadow: 0 14px 34px rgba(0,0,0,0.18);
  }
  /* Front */
  .card-front {
    background: linear-gradient(135deg, var(--blue-light) 0%, var(--blue-deep) 100%);
    display: flex;
    align-items: center;
    justify-content: center;
  }
  .brand {
    display: flex;
    align-items: center;
    gap: 14px;
  }
  .brand-dot {
    width: 34px; height: 34px;
    border-radius: 50%;
  }
  .brand-name {
    font-weight: 400;
    letter-spacing: 1px;
  }
  .card-front .brand-dot { background: var(--white); }
  .card-front .brand-name { color: var(--white); font-size: 40px; }

  /* Back */
  .card-back { background: var(--white); }
  .faint-circle {
    position: absolute;
    right: 40px; top: -40px;
    width: 200px; height: 200px;
    border-radius: 50%;
    background: var(--faint-circle);
  }
  .card-back .brand {
    position: absolute;
    left: 36px; top: 58px;
  }
  .card-back .brand-dot { background: var(--blue-brand); width: 40px; height: 40px; }
  .card-back .brand-name { color: var(--blue-brand); font-size: 38px; }

  .person {
    position: absolute;
    left: 36px; top: 158px;
  }
  .person-name {
    color: var(--blue-brand);
    font-weight: 700;
    font-size: 22px;
  }
  .person-role {
    color: var(--ink);
    font-size: 14px;
    margin-top: 4px;
  }
  .rule {
    position: absolute;
    left: 36px; right: 36px; top: 222px;
    height: 1px;
    background: var(--rule);
  }
  .phone {
    position: absolute;
    top: 236px;
    display: flex;
    align-items: center;
    gap: 7px;
    color: var(--ink);
    font-size: 13px;
  }
  .phone-spain { left: 36px; }
  .phone-usa { right: 36px; }
  .phone-icon { width: 15px; height: 15px; }

  .stripe-green {
    position: absolute;
    left: 0; bottom: 0;
    width: 330px; height: 10px;
    background: linear-gradient(90deg, var(--green-brand), var(--green-light));
  }
  .web-band {
    position: absolute;
    right: 0; bottom: 0;
    width: 195px; height: 30px;
    background: linear-gradient(90deg, var(--blue-brand), var(--blue-light));
    color: var(--white);
    font-size: 11.5px;
    display: flex;
    align-items: center;
    justify-content: center;
  }
</style>
</head>
<body>
  <section class="card card-front" aria-label="Card front">
    <div class="brand">
      <span class="brand-dot"></span>
      <span class="brand-name">Dorian Vitality</span>
    </div>
  </section>

  <section class="card card-back" aria-label="Card back">
    <div class="faint-circle"></div>
    <div class="brand">
      <span class="brand-dot"></span>
      <span class="brand-name">Dorian Vitality</span>
    </div>
    <div class="person">
      <p class="person-name">Tomás Lirandel</p>
      <p class="person-role">Coach, Consultant &amp; Trainer.</p>
    </div>
    <div class="rule"></div>
    <p class="phone phone-spain">
      <svg class="phone-icon" viewBox="0 0 16 16" aria-hidden="true">
        <circle cx="8" cy="8" r="8" fill="#1f78c8"/>
        <path d="M5.6 4.2l1.3 1.6-.7.9c.5 1.1 1.3 1.9 2.4 2.4l.9-.7 1.6 1.3-.7 1.4c-2.9-.3-5.1-2.5-5.4-5.4z" fill="#fff"/>
      </svg>
      Spain (+34) 612 480 317
    </p>
    <p class="phone phone-usa">
      <svg class="phone-icon" viewBox="0 0 16 16" aria-hidden="true">
        <circle cx="8" cy="8" r="8" fill="#1f78c8"/>
        <path d="M5.6 4.2l1.3 1.6-.7.9c.5 1.1 1.3 1.9 2.4 2.4l.9-.7 1.6 1.3-.7 1.4c-2.9-.3-5.1-2.5-5.4-5.4z" fill="#fff"/>
      </svg>
      (USA) +1 (555) 610 4829
    </p>
    <div class="stripe-green"></div>
    <p class="web-band">www.dorianvitality-example.com</p>
  </section>
</body>
</html>
```